Kestrel Home Business Card Design

We need a business card for a Building company based in Queensland, Australia. Our colours are orange black and we do base all our homes design names and other aspect of our business on astrology. We want the consumer to perceive the company as professional and to attract investors to our company.We have over 20 years in the building industry.We pride ourselves on our innovation of designs and making the building process for anyone from families to investor a smooth and simple experience.
Business
Amelia Prichard0411752116PO Box 454, Mudgeerbaameliaprichard@zodiachomes.com

```html
<!DOCTYPE html>
<html lang="en">
<head>
<meta charset="utf-8">
<title>Kestrel Homes Business Card</title>
<link rel="stylesheet" href="https://fonts.googleapis.com/css2?family=Montserrat:wght@700&family=Questrial&family=Open+Sans:wght@400&display=swap">
<style>
  :root {
    --canvas-bg: #e9ebec;
    --card-white: #ffffff;
    --brand-orange: #f28a1c;
    --brand-orange-deep: #ec6f12;
    --ink: #1c1c1c;
    --ink-soft: #3a3a3a;
    --card-shadow: rgba(0, 0, 0, 0.14);
  }
  * { margin: 0; padding: 0; box-sizing: border-box; }
  html, body {
    width: 1200px;
    height: 900px;
    overflow: hidden;
    background: var(--canvas-bg);
  }
  .canvas {
    width: 1200px;
    height: 900px;
    display: flex;
    align-items: center;
    justify-content: center;
    gap: 60px;
  }
  .card {
    width: 520px;
    height: 300px;
    position: relative;
    box-shadow: 0 10px 28px var(--card-shadow);
    overflow: hidden;
  }

  /* Front: contact side */
  .card-front { background: var(--card-white); }
  .brand-row {
    position: absolute;
    left: 38px;
    top: 66px;
    display: flex;
    align-items: center;
    gap: 14px;
  }
  .brand-dot {
    width: 46px;
    height: 46px;
    border-radius: 50%;
    background: var(--brand-orange);
  }
  .brand-name {
    font-family: "Montserrat", sans-serif;
    font-weight: 700;
    font-size: 24px;
    color: var(--ink);
    letter-spacing: 0.2px;
  }
  .brand-rule {
    position: absolute;
    left: 270px;
    right: 0;
    top: 74px;
    height: 1.5px;
    background: var(--brand-orange);
  }
  .holder-name {
    position: absolute;
    left: 38px;
    top: 150px;
    font-family: "Questrial", sans-serif;
    font-size: 25px;
    color: var(--ink);
    letter-spacing: 0.6px;
  }
  .holder-rule {
    position: absolute;
    left: 38px;
    width: 250px;
    top: 190px;
    height: 1.5px;
    background: var(--brand-orange);
  }
  .contact-list {
    position: absolute;
    left: 38px;
    top: 204px;
    list-style: none;
    font-family: "Open Sans", sans-serif;
    font-size: 12px;
    color: var(--ink-soft);
    line-height: 20px;
  }
  .contact-list li { display: flex; align-items: center; gap: 8px; }
  .contact-icon { width: 11px; height: 11px; flex: none; }

  /* Back: brand side */
  .card-back {
    background: linear-gradient(135deg, var(--brand-orange) 0%, var(--brand-orange-deep) 100%);
    display: flex;
    flex-direction: column;
    align-items: center;
    justify-content: center;
    gap: 20px;
  }
  .back-dot {
    width: 96px;
    height: 96px;
    border-radius: 50%;
    background: var(--ink);
  }
  .back-name {
    font-family: "Montserrat", sans-serif;
    font-weight: 700;
    font-size: 40px;
    color: var(--ink);
  }
</style>
</head>
<body>
<main class="canvas">
  <section class="card card-front" aria-label="Business card front">
    <div class="brand-row">
      <span class="brand-dot"></span>
      <span class="brand-name">Kestrel Homes</span>
    </div>
    <div class="brand-rule"></div>
    <p class="holder-name">Harriet Colvane</p>
    <div class="holder-rule"></div>
    <ul class="contact-list">
      <li>
        <svg class="contact-icon" viewBox="0 0 24 24" aria-hidden="true"><path fill="#f28a1c" d="M6.6 10.8a15.1 15.1 0 0 0 6.6 6.6l2.2-2.2a1 1 0 0 1 1-.25 11.4 11.4 0 0 0 3.6.57 1 1 0 0 1 1 1V20a1 1 0 0 1-1 1A17 17 0 0 1 3 4a1 1 0 0 1 1-1h3.5a1 1 0 0 1 1 1c0 1.25.2 2.45.57 3.57a1 1 0 0 1-.25 1z"/></svg>
        <span>0487309625</span>
      </li>
      <li>
        <svg class="contact-icon" viewBox="0 0 24 24" aria-hidden="true"><path fill="#f28a1c" d="M12 2a7 7 0 0 0-7 7c0 5.2 7 13 7 13s7-7.8 7-13a7 7 0 0 0-7-7zm0 9.5A2.5 2.5 0 1 1 12 6.5a2.5 2.5 0 0 1 0 5z"/></svg>
        <span>PO Box 872, Wattle Ridge</span>
      </li>
      <li>
        <svg class="contact-icon" viewBox="0 0 24 24" aria-hidden="true"><path fill="none" stroke="#f28a1c" stroke-width="2" d="M3 5h18v14H3z M3 5l9 8 9-8"/></svg>
        <span>harrietcolvane@kestrelhomes.example</span>
      </li>
    </ul>
  </section>

  <section class="card card-back" aria-label="Business card back">
    <span class="back-dot"></span>
    <span class="back-name">Kestrel Homes</span>
  </section>
</main>
</body>
</html>
```